Awesome business card design needed

We need a new business card design to go with our new logo.
We are a web development agency that specialises in highly complex back-end integrations as opposed to design, our customers are retailers, hotels, hospitals and any other organisation that has a large online marketing department.
Take a look at our website - www.brenoloft.com for some inspiration.
We want our new business cards to exude class, professionalism and style.
We are likely to choose a high-end card to print them on but we want the design of the card itself to really turn heads.
We have no specific colour requirements, the logo as you will see is a turquoise colour R89 G171 B167 #59aba7 but it can also be in white if you want to make the colour of the card something different.
The information on the card should be:
Name
Position
Tel
email
Potentially a double sided card could have our web address, twitter and FB links.

```html
<!DOCTYPE html>
<html lang="en">
<head>
<meta charset="utf-8">
<title>Brenoloft business card</title>
<link rel="stylesheet" href="https://fonts.googleapis.com/css2?family=Roboto+Condensed:wght@700&family=PT+Serif&display=swap">
<style>
  :root {
    --backdrop: #e8e5e1;
    --paper: #ffffff;
    --ink: #111111;
    --teal: #59aba7;
    --teal-deep: #468b88;
    --teal-pale: #d3e5e4;
    --teal-ghost: #cfe2e1;
    --band-ink: #1c3433;
    --card-dark: #262626;
    --white: #ffffff;
  }
  * { margin: 0; padding: 0; box-sizing: border-box; }
  html, body { width: 1200px; height: 1000px; overflow: hidden; }
  body { background: var(--backdrop); position: relative; }

  .card { position: absolute; width: 694px; height: 402px; overflow: hidden; box-shadow: 0 4px 14px rgba(0,0,0,.25); }
  .card--front { left: 398px; top: 50px; background: var(--paper); }
  .card--back { left: 203px; top: 473px; background: var(--card-dark); }

  .holder { position: absolute; left: 42px; top: 24px; font-family: "Roboto Condensed", sans-serif; font-weight: 700; color: var(--ink); }
  .holder__name { font-size: 35px; line-height: 1.05; }
  .holder__role { font-size: 22px; line-height: 1.1; }

  .contact { position: absolute; left: 0; height: 25px; background: var(--teal-pale);
    clip-path: polygon(0 0, calc(100% - 26px) 0, 100% 100%, 0 100%); }
  .contact--phone { top: 283px; width: 254px; }
  .contact--mail { top: 315px; width: 284px; }
  .contact--web { top: 348px; width: 312px; }
  .contact__icon { position: absolute; left: 46px; top: 3px; width: 20px; height: 20px; }
  .contact__text { position: absolute; left: 86px; top: 0; line-height: 25px; font-family: "PT Serif", serif; font-size: 20px; color: var(--ink); white-space: nowrap; }

  .watermark { position: absolute; left: 420px; top: 25px; width: 62px; height: 350px;
    writing-mode: vertical-rl; transform: rotate(180deg); font-family: "Roboto Condensed", sans-serif;
    font-weight: 700; font-size: 62px; line-height: 62px; text-align: center; color: var(--teal-ghost); }

  .social { position: absolute; top: 0; width: 93px; height: 100%; }
  .social--one { left: 508px; background: var(--teal-deep); }
  .social--two { left: 601px; background: var(--teal); }
  .social__handle { position: absolute; left: 24px; top: 28px; height: 280px; writing-mode: vertical-rl;
    transform: rotate(180deg); font-family: "PT Serif", serif; font-size: 23px; line-height: 46px; color: var(--band-ink); text-align: left; }
  .social__mark { position: absolute; left: 19px; top: 326px; width: 48px; height: 48px; }
  .social--one .social__mark { background: var(--white); }
  .social--two .social__mark { background: var(--teal-deep); }

  .back__logo { position: absolute; left: 46px; top: 142px; font-family: "Roboto Condensed", sans-serif;
    font-weight: 700; font-size: 84px; line-height: 1; color: var(--white); letter-spacing: 1px; }
  .back__strip { position: absolute; height: 15px; background: var(--teal); }
  .back__strip--top { right: 0; top: 0; width: 232px; clip-path: polygon(14px 0, 100% 0, 100% 100%, 0 100%); }
  .back__strip--bottom { left: 0; bottom: 0; width: 240px; clip-path: polygon(0 0, 100% 0, calc(100% - 14px) 100%, 0 100%); }
</style>
</head>
<body>
  <section class="card card--front">
    <div class="holder">
      <div class="holder__name">Alex Morgan</div>
      <div class="holder__role">Your designation</div>
    </div>

    <div class="contact contact--phone">
      <svg class="contact__icon" viewBox="0 0 24 24" aria-hidden="true"><path fill="#111" d="M6.6 2.5l3 3.6-1.9 2.4c1.3 2.9 3.6 5.3 6.6 6.7l2.4-1.9 3.6 3-1.8 3.2C11.6 19.2 4.8 12.4 3.4 4.3z"/></svg>
      <span class="contact__text">0198765432</span>
    </div>
    <div class="contact contact--mail">
      <svg class="contact__icon" viewBox="0 0 24 24" aria-hidden="true"><rect x="2" y="5" width="20" height="14" fill="#111"/><path d="M2.5 6l9.5 7 9.5-7M2.5 18.5l7-6M21.5 18.5l-7-6" stroke="#fff" stroke-width="1.4" fill="none"/></svg>
      <span class="contact__text">alex@brenoloft.com</span>
    </div>
    <div class="contact contact--web">
      <svg class="contact__icon" viewBox="0 0 24 24" aria-hidden="true"><g fill="none" stroke="#111" stroke-width="1.6"><circle cx="12" cy="12" r="9"/><ellipse cx="12" cy="12" rx="4" ry="9"/><path d="M3 12h18M5 7h14M5 17h14"/></g></svg>
      <span class="contact__text">www.brenoloft.com</span>
    </div>

    <div class="watermark" aria-hidden="true">brenoloft</div>

    <div class="social social--one">
      <div class="social__handle">social.brenoloft.com</div>
      <div class="social__mark" aria-hidden="true"></div>
    </div>
    <div class="social social--two">
      <div class="social__handle">news.brenoloft.com</div>
      <div class="social__mark" aria-hidden="true"></div>
    </div>
  </section>

  <section class="card card--back">
    <div class="back__strip back__strip--top"></div>
    <div class="back__logo">brenoloft</div>
    <div class="back__strip back__strip--bottom"></div>
  </section>
</body>
</html>
```